Modern & Fresh Vantacor Book Cover

Need a creative e-book cover for my book.

Title: Master Vantacor Fast
Subtitle: Learn How To Easily Choose & Enroll in the Perfect Coverage at the Perfect Time.

Target Market(s)

60-70 year olds in the United States

Font styles to use
Sans Serif

Colors
9bcb3c
33a6d7

Requirements
Must have
• Must look modern and fresh.
• Use our company colors www.Movaquill.com

```html
<!DOCTYPE html>
<html lang="en">
<head>
<meta charset="utf-8">
<title>Master Vantacor Fast – Book Cover</title>
<link href="https://fonts.googleapis.com/css2?family=Anton&family=Montserrat:wght@400;700&family=Oswald:wght@500&display=swap" rel="stylesheet">
<style>
  :root {
    --cover-bg: #ffffff;
    --brand-blue: #2c7bbd;
    --rule-blue: #6aa0d0;
    --brand-green: #7cac3b;
    --subtitle-ink: #444444;
    --art-light: #f3f6f9;
    --art-mid: #dfe8f1;
  }
  html, body {
    margin: 0;
    padding: 0;
    overflow: hidden;
    background: var(--cover-bg);
  }
  .cover {
    position: relative;
    width: 800px;
    height: 1200px;
    background: var(--cover-bg);
    overflow: hidden;
  }
  .title-block {
    position: absolute;
    left: 0;
    top: 0;
    width: 800px;
    height: 610px;
  }
  .title-lead {
    font-family: "Montserrat", sans-serif;
    font-weight: 700;
    fill: var(--brand-blue);
  }
  .title-rule {
    stroke: var(--rule-blue);
    stroke-width: 4;
  }
  .title-main {
    font-family: "Anton", sans-serif;
    fill: var(--brand-green);
  }
  .title-punch {
    font-family: "Anton", sans-serif;
    fill: var(--brand-blue);
  }
  .subtitle {
    position: absolute;
    left: 60px;
    top: 619px;
    width: 680px;
    margin: 0;
    font-family: "Montserrat", sans-serif;
    font-weight: 400;
    font-size: 21.5px;
    line-height: 30px;
    letter-spacing: 0.3px;
    text-align: center;
    color: var(--subtitle-ink);
  }
  .cover-art {
    position: absolute;
    left: 225px;
    top: 692px;
    width: 392px;
    height: 388px;
    border-radius: 12px;
    background: radial-gradient(ellipse at 50% 55%, var(--art-mid), var(--art-light) 75%);
  }
  .author-name {
    position: absolute;
    left: 0;
    top: 1106px;
    width: 800px;
    margin: 0;
    font-family: "Oswald", sans-serif;
    font-weight: 500;
    font-size: 50px;
    line-height: 58px;
    letter-spacing: 8px;
    text-indent: 8px;
    text-align: center;
    color: var(--brand-blue);
  }
</style>
</head>
<body>
  <main class="cover">
    <svg class="title-block" viewBox="0 0 800 610" role="heading" aria-level="1" aria-label="Master Vantacor Fast">
      <line class="title-rule" x1="94" y1="100" x2="190" y2="100"/>
      <line class="title-rule" x1="610" y1="100" x2="706" y2="100"/>
      <text class="title-lead" x="210" y="146" font-size="110" textLength="380" lengthAdjust="spacingAndGlyphs">MASTER</text>
      <text class="title-main" x="81" y="307" font-size="155" textLength="636" lengthAdjust="spacingAndGlyphs">VANTACOR</text>
      <text class="title-punch" x="81" y="595" font-size="310" textLength="638" lengthAdjust="spacingAndGlyphs">FAST</text>
    </svg>

    <p class="subtitle">Learn How To Easily Choose &amp; Enroll in the Perfect<br>Coverage at the Perfect Time.</p>

    <div class="cover-art" role="img" aria-label="Illustration of an older woman pushing a smiling older man in a wheelchair"></div>

    <p class="author-name">AUTHOR NAME</p>
  </main>
</body>
</html>
```